Popup Nightclub Grand Opening Flyer

We need to design a flyer for the grand opening of an upscale, exclusive nightclub called "Lantern". The design needs to be chic and exclusive. The background should be black and the text should primarily be white. We like minimalist designs.

Here is the text for the flyer
-
Velvetroll Atlanta Presents

Lantern (LOGO)

A Popup Nightclub Experience
For one night Only

Friday, October 18, 2013
Party begins at 9PM

INVITE ONLY

See invitation for location details
(Velvetroll Atlanta logo)

-
Examples we like

http://cdn4-x.pressfolio-example.com/sites/default/files/styles/image_content_width/hash/3b/fd/2468013579_4421_flyer.jpg?itok=K9rtQw2z

http://files.hubspace-example.net/files/8Hqq-Tr72WWE3kaRbTmcxP5QZK2F396J8nbRw4CKMHfdX2Y7qSEF-MqjxDoNrLY3QCyQJD7npjGaRq3k-Mhx6hqf3MDSWf8r3/2zenSaturdays.jpg

http://morvex-example.com/wp-content/uploads/siteskin/widgetkit/gallery/2zen/2zen-gen_qstay4-01.jpg

Hi All, one thing that we are seeing that we don't like is on over emphasis on the phrase "a popup nightclub experience" please don't make this the largest thing on the flyer

Target Market(s)

Target market is 25-35 year olds who are affluent (rich) and like luxury brands

Requirements
Must have
• Dark Background
Nice to have
• Velvetroll Logo on the bottom
Modern text that isn't curvy
Should not have
• Curved text

```html
<!DOCTYPE html>
<html lang="en">
<head>
<meta charset="utf-8">
<title>Lantern Nightclub — Velvetroll Atlanta Presents</title>
<link rel="stylesheet" href="https://fonts.googleapis.com/css2?family=Montserrat:wght@300;600;700&display=swap">
<style>
  :root {
    --ink: #000000;
    --damask: #1c1c1c;
    --damask-deep: #0b0b0b;
    --white: #ffffff;
    --soft-white: #e6e6e6;
    --gold: #c9c21c;
    --gold-glow: rgba(214, 205, 30, 0.55);
    --grey: #8c8c8c;
    --rule: #cfcfcf;
    --mark: #2a2a2a;
  }
  * { margin: 0; padding: 0; box-sizing: border-box; }
  html, body {
    width: 787px;
    height: 1200px;
    overflow: hidden;
    background: var(--ink);
  }
  .flyer {
    position: relative;
    width: 787px;
    height: 1200px;
    background: var(--ink);
    font-family: "Montserrat", Arial, sans-serif;
    color: var(--white);
    text-align: center;
    overflow: hidden;
  }
  .damask-field {
    position: absolute;
    inset: 0 0 auto 0;
    height: 960px;
    background:
      radial-gradient(ellipse 70% 55% at 50% 35%, var(--damask) 0%, var(--damask-deep) 70%, transparent 100%),
      linear-gradient(180deg, var(--damask-deep) 0%, var(--damask) 40%, var(--ink) 100%);
  }
  .block {
    position: absolute;
    left: 0;
    width: 100%;
  }
  .presenter {
    top: 40px;
    font-size: 19px;
    font-weight: 700;
    letter-spacing: 0.3px;
    color: var(--soft-white);
  }
  .club-mark {
    position: absolute;
    left: 50%;
    top: 150px;
    transform: translateX(-50%);
  }
  .club-name {
    top: 640px;
    font-weight: 300;
    color: var(--white);
    line-height: 1;
  }
  .club-name .name {
    display: block;
    font-size: 50px;
    letter-spacing: 9px;
  }
  .club-name .kind {
    display: block;
    margin-top: 10px;
    font-size: 24px;
    letter-spacing: 5px;
  }
  .tagline {
    top: 752px;
    font-size: 35px;
    font-weight: 700;
    letter-spacing: 0.2px;
  }
  .rule {
    position: absolute;
    left: 83px;
    width: 621px;
    top: 806px;
    height: 2px;
    background: var(--rule);
  }
  .one-night {
    top: 830px;
    font-size: 53px;
    font-weight: 700;
    color: var(--gold);
    text-shadow: 0 0 14px var(--gold-glow), 0 0 28px var(--gold-glow);
    letter-spacing: 0.5px;
  }
  .date-time {
    top: 904px;
    font-size: 27px;
    font-weight: 700;
    color: var(--grey);
    letter-spacing: 1px;
  }
  .access {
    top: 1016px;
    font-size: 26px;
    font-weight: 700;
  }
  .access-note {
    top: 1060px;
    font-size: 12px;
    font-weight: 700;
    letter-spacing: 0.2px;
  }
  .host-sign {
    top: 1112px;
    font-size: 26px;
    font-weight: 300;
    letter-spacing: 3px;
    color: var(--soft-white);
  }
</style>
</head>
<body>
  <main class="flyer">
    <div class="damask-field" role="img" aria-label="Dark black-on-black damask scroll pattern background"></div>

    <p class="block presenter">VELVETROLL ATLANTA PRESENTS</p>

    <svg class="club-mark" width="380" height="420" viewBox="0 0 380 420" aria-hidden="true">
      <circle cx="190" cy="250" r="160" fill="var(--mark)"/>
    </svg>

    <h1 class="block club-name">
      <span class="name">LANTERN</span>
      <span class="kind">NIGHTCLUB</span>
    </h1>

    <h2 class="block tagline">A POPUP NIGHTCLUB EXPERIENCE</h2>
    <div class="rule"></div>

    <p class="block one-night">FOR ONE NIGHT ONLY</p>
    <p class="block date-time">FRIDAY OCTOBER 18 2013 @ 9:00PM</p>

    <p class="block access">INVITE ONLY</p>
    <p class="block access-note">SEE INVITATION FOR LOCATION DETAILS</p>

    <p class="block host-sign">VELVETROLL ATLANTA</p>
  </main>
</body>
</html>
```